Conference flyer

We need a flyer for a conference for the defence industry. The attached has been updated with new information using last years flyer. We would like something new and fresh. Please note the theme of the conference is 'a global environment'.

The final design should reflect the defence industry and manufacturing.

Industry/Entity Type

Defence

```html
<!DOCTYPE html>
<html lang="en">
<head>
<meta charset="utf-8">
<title>Defence Trade Controls Conference 2015</title>
<link href="https://fonts.googleapis.com/css2?family=Oswald:wght@400;500&family=Open+Sans:wght@400;600;700;800&display=swap" rel="stylesheet">
<style>
  :root {
    --olive-dark: #3b3c17;
    --olive-mid: #5e5f27;
    --olive-light: #8a8a45;
    --lime: #8c9b2f;
    --lime-light: #a5b43f;
    --cream: #eef0d6;
    --ink: #1b1b1b;
    --paper: #ffffff;
    --logo-grey: #555a60;
  }
  * { margin: 0; padding: 0; box-sizing: border-box; }
  html, body { width: 848px; height: 1200px; overflow: hidden; background: var(--paper); }
  .flyer {
    position: relative; width: 848px; height: 1200px; overflow: hidden;
    font-family: "Open Sans", Arial, sans-serif; background: var(--paper);
  }
  .hero-bg { position: absolute; inset: 0; width: 848px; height: 720px; }
  .title-band {
    position: absolute; top: 0; left: 0; width: 848px; height: 103px;
    display: flex; align-items: center; justify-content: center;
    background: linear-gradient(180deg, #46471c, #5a5b26);
  }
  .event-title {
    font-family: "Oswald", "Arial Narrow", sans-serif; font-weight: 400;
    color: var(--paper); font-size: 55px; letter-spacing: 0.2px; line-height: 1;
  }
  .theme-band {
    position: absolute; top: 109px; left: 0; width: 848px; height: 56px;
    background: linear-gradient(180deg, var(--lime-light), var(--lime));
    display: flex; align-items: center; justify-content: center;
  }
  .theme {
    color: var(--paper); font-weight: 700; font-size: 29px; letter-spacing: 0.4px;
  }
  .globe {
    position: absolute; left: 265px; top: 148px; width: 610px; height: 610px;
    border-radius: 50%; border: 10px solid var(--paper);
    background: radial-gradient(circle at 45% 40%, #9a9a5a 0%, #6f6f35 45%, #3e3f1a 100%);
    box-shadow: 0 0 18px rgba(0,0,0,.35);
  }
  .intro {
    position: absolute; left: 37px; top: 228px; width: 250px;
    color: var(--cream); font-weight: 600; font-size: 24px; line-height: 33px;
  }
  .dates {
    position: absolute; left: 37px; top: 610px;
    color: var(--paper); font-weight: 700; font-size: 25px;
  }
  .speakers { position: absolute; left: 26px; top: 770px; width: 800px; }
  .speakers-heading {
    font-weight: 800; font-size: 19.5px; color: var(--ink); margin-bottom: 22px; letter-spacing: .2px;
  }
  .speaker-list { list-style: none; }
  .speaker { font-size: 15px; color: var(--ink); height: 41.5px; }
  .speaker-name { font-weight: 700; font-size: 18px; }
  .partners {
    position: absolute; left: 0; top: 1086px; width: 848px; height: 80px;
    display: flex; align-items: center; justify-content: space-around; padding: 0 20px;
  }
  .partner {
    display: flex; align-items: center; gap: 8px;
    font-weight: 700; font-size: 17px; color: var(--logo-grey);
  }
  .partner-dot { width: 16px; height: 16px; border-radius: 50%; background: var(--lime); }
  .footer-band {
    position: absolute; left: 0; bottom: 0; width: 848px; height: 14px;
    background: var(--olive-mid);
  }
</style>
</head>
<body>
<div class="flyer">
  <svg class="hero-bg" viewBox="0 0 848 720" aria-hidden="true">
    <defs>
      <radialGradient id="heroGlow" cx="0.3" cy="0.55" r="0.8">
        <stop offset="0" stop-color="#7f7f3c"/>
        <stop offset="0.6" stop-color="#55561f"/>
        <stop offset="1" stop-color="#3a3b16"/>
      </radialGradient>
      <linearGradient id="sweep" x1="0" y1="0" x2="1" y2="0">
        <stop offset="0" stop-color="#9ca545"/>
        <stop offset="1" stop-color="#6d7028"/>
      </linearGradient>
    </defs>
    <rect width="848" height="720" fill="url(#heroGlow)"/>
    <path d="M0 640 C 120 660 260 690 420 700 L 420 720 L 0 720 Z" fill="url(#sweep)"/>
    <path d="M0 672 C 140 690 280 710 440 715 L 848 720 L 0 720 Z" fill="#ffffff"/>
  </svg>

  <header class="title-band">
    <h1 class="event-title">DEFENCE TRADE CONTROLS CONFERENCE</h1>
  </header>
  <div class="theme-band">
    <h2 class="theme">TRADE CONTROLS IN A GLOBAL ENVIRONMENT</h2>
  </div>

  <div class="globe" role="img" aria-label="Globe showing Africa, Asia and Australia linked by glowing dashed trade routes"></div>

  <p class="intro">Presenting the DTC 2015 Conference Australia’s annual defence industry global trade controls conference</p>
  <p class="dates">2 &amp; 3 June, 2015</p>

  <section class="speakers">
    <h3 class="speakers-heading">FEATURING PRESENTATIONS FROM:</h3>
    <ul class="speaker-list">
      <li class="speaker"><span class="speaker-name">Hannah Carlisle</span> Assistant Secretary, Defence Export Licensing Office</li>
      <li class="speaker"><span class="speaker-name">Renee Whitmore</span> Managing Director, Whitmore Trade Advisors LLC</li>
      <li class="speaker"><span class="speaker-name">Dylan Prescott</span> Director Compliance, Commercial and Policy Allied Materiel Sales Office</li>
      <li class="speaker"><span class="speaker-name">Peter Vasilakis</span> Import/Export Compliance Manager, Corvane Systems Australia</li>
      <li class="speaker"><span class="speaker-name">Lin Zhao</span> Global Trade Compliance Director, Semiconductors</li>
      <li class="speaker"><span class="speaker-name">Owen Falkner</span> Partner, Meridian Compliance Strategies</li>
    </ul>
  </section>

  <footer class="partners">
    <div class="partner"><span class="partner-dot"></span>Southcoast Defence Network</div>
    <div class="partner">Harbourline Industry Group</div>
    <div class="partner">Veridane</div>
    <div class="partner"><span class="partner-dot"></span>Exportwise Centre</div>
  </footer>
  <div class="footer-band"></div>
</div>
</body>
</html>
```